Buchcover-Design für Erziehungsratgeber
Zielgruppe
Es handelt sich um einen Erziehungsratgeber zum Thema 'bedürfnisorientierte Erziehung'.
Zielgruppe :
Frauen 25-35 Jahre
Werdende Mütter bzw. Mütter eines Neugeborenen
Personen mit Vorliebe für natürliche Heilmittel, Methoden oder Konzepte.
Personen, die eher Vorbehalte ggü. chemischen, kommerziellen oder industriellen Heilmitteln, Methoden, Konzepten haben.
Aufgabenstellung
Das Cover soll ein Baby 1-12 Monate zeigen, ggf. auch mit der Mutter zusammen.
Das Cover soll Schutz, Geborgenheit und Fürsorge ausstrahlen.
Eine kreativere Titel-Anordnung ist gewünscht. Bitte wählen Sie für die Titel-Anordnung KEINE Standard-Anordnung, also z.B. nicht mittig zentriert im oberen Drittel.
Farbvorschlag für den Titel-Text: 800080ff (abweichende Ideen sind trotzdem gern gesehen)
Stockmaterial wird von Bildquellfarm.com bevorzugt.
Cover-Maße: 6x9 Zoll, 170 Seiten. Bitte Template benutzen.
Das Verlagslogo soll unten Links auf dem Cover abgedruckt werden. Bitte wählen Sie eine zum Cover passende, unauffällige Farbe.
Titel: 'Kleine Schritte im warmen Nest des Familienalltags'
Sub-Titel (unauffällig darstellen): 'Wie Sie mit natürlichen Erziehungsmethoden Ihr Kind bestmöglich großziehen und verstehen, was Ihr Baby wirklich braucht. Ein Erziehungsratgeber für Babys von 0-12 Monaten'
Autoren-Name: 'Helga Sturm'

```html
<!DOCTYPE html>
<html lang="de">
<head>
<meta charset="utf-8">
<title>Kleine Schritte im warmen Nest des Familienalltags – Buchumschlag</title>
<link rel="stylesheet" href="https://fonts.googleapis.com/css2?family=Amatic+SC:wght@700&family=Roboto:wght@400;500&display=swap">
<style>
  :root {
    --back-violet: #bf7fbf;
    --spine-purple: #800080;
    --title-purple: #800080;
    --paper-white: #ffffff;
    --photo-window: #f2f1ef;
    --photo-room: #ebe6e3;
    --photo-warm: #e8d3cc;
    --photo-bed: #f5f4f3;
    --publisher-grey: #4a4a4a;
    --subtitle-grey: #5e4a5e;
  }
  * { margin: 0; padding: 0; box-sizing: border-box; }
  html, body { width: 1200px; height: 874px; overflow: hidden; background: var(--paper-white); }
  .cover-wrap {
    position: relative;
    width: 1200px;
    height: 874px;
    font-family: "Roboto", Arial, sans-serif;
  }

  /* Rückseite */
  .back-cover {
    position: absolute; left: 0; top: 0;
    width: 579px; height: 874px;
    background: var(--back-violet);
    color: var(--paper-white);
  }
  .back-title {
    position: absolute; left: 40px; top: 100px; width: 500px;
    text-align: center;
    font-weight: 500; font-size: 21px; line-height: 33px;
    letter-spacing: 0.8px; text-transform: uppercase;
  }
  .back-blurb {
    position: absolute; left: 67px; top: 179px; width: 452px;
    font-size: 14.8px; line-height: 23.6px; letter-spacing: 0.55px;
  }
  .barcode-area {
    position: absolute; left: 365px; top: 727px;
    width: 191px; height: 115px;
    background: var(--paper-white);
  }

  /* Buchrücken */
  .spine {
    position: absolute; left: 579px; top: 0;
    width: 36px; height: 874px;
    background: var(--spine-purple);
    color: var(--paper-white);
  }
  .spine-text {
    position: absolute; left: 50%;
    white-space: nowrap;
    font-weight: 500; font-size: 14.5px; letter-spacing: 1px;
    text-transform: uppercase;
    transform-origin: left center;
  }
  .spine-title { top: 624px; transform: translateX(7px) rotate(-90deg); }
  .spine-author { top: 828px; transform: translateX(7px) rotate(-90deg); }

  /* Vorderseite */
  .front-cover {
    position: absolute; left: 615px; top: 0;
    width: 585px; height: 874px;
    overflow: hidden;
  }
  .front-photo {
    position: absolute; inset: 0;
    background: linear-gradient(160deg,
      var(--photo-window) 0%,
      var(--photo-room) 40%,
      var(--photo-warm) 62%,
      var(--photo-bed) 100%);
  }
  .front-title {
    position: absolute; left: 34px; top: 116px;
    color: var(--title-purple);
    font-family: "Amatic SC", "Arial Narrow", sans-serif;
    font-weight: 700;
    text-transform: uppercase;
    line-height: 1;
  }
  .front-title .line { display: block; white-space: nowrap; letter-spacing: 2px; }
  .front-title .line-small { font-size: 50px; }
  .front-title .line-big { font-size: 86px; margin-top: -6px; }
  .front-title .word-small { font-size: 40px; }
  .front-subtitle {
    position: absolute; left: 36px; top: 418px; width: 300px;
    color: var(--subtitle-grey);
    font-size: 12.5px; line-height: 18px; letter-spacing: 0.2px;
  }
  .publisher-name {
    position: absolute; left: 36px; top: 809px;
    color: var(--publisher-grey);
    font-size: 20px; font-weight: 500; letter-spacing: 0.5px;
  }
  .front-author {
    position: absolute; left: 190px; top: 809px;
    color: var(--title-purple);
    font-size: 29px; font-weight: 500; letter-spacing: 1.5px;
    text-transform: uppercase;
  }
</style>
</head>
<body>
<div class="cover-wrap">
  <section class="back-cover">
    <h2 class="back-title">Kleine Schritte im warmen Nest<br>des Familienalltags</h2>
    <p class="back-blurb">Lorem ipsum dolor sit amet, consectetuer adipiscing elit. Aenean commodo ligula eget dolor. Aenean massa. Cum sociis natoque penatibus et magnis dis parturient montes, nascetur ridiculus mus. Donec quam felis, ultricies nec, pellentesque eu, pretium quis, sem. Nulla consequat massa quis enim. Donec pede justo, fringilla vel, aliquet nec, vulputate eget, arcu. In enim justo, rhoncus ut, imperdiet a, venenatis vitae, justo. Nullam dictum felis eu pede mollis pretium. Integer tincidunt. Cras dapibus. Vivamus elementum semper nisi. Aenean vulputate eleifend tellus. Aenean leo ligula, porttitor eu, consequat vitae, eleifend ac, enim. Aliquam lorem ante, dapibus in, viverra quis, feugiat a, tellus.</p>
    <div class="barcode-area"></div>
  </section>

  <section class="spine">
    <span class="spine-text spine-title">Kleine Schritte im warmen Nest des Familienalltags</span>
    <span class="spine-text spine-author">Helga Sturm</span>
  </section>

  <section class="front-cover">
    <div class="front-photo" role="img" aria-label="Foto: Mutter im lachsroten T-Shirt hält die Beinchen ihres Babys, das auf einem weißen Bett in einem hellen Zimmer liegt"></div>
    <h1 class="front-title">
      <span class="line line-small">Kleine Schritte im</span>
      <span class="line line-big">Warmen Nest <span class="word-small">des</span></span>
      <span class="line line-big">Familien-</span>
      <span class="line line-big">alltags</span>
    </h1>
    <p class="front-subtitle">Wie Sie mit natürlichen Erziehungsmethoden Ihr Kind bestmöglich großziehen und verstehen, was Ihr Baby wirklich braucht. Ein Erziehungsratgeber für Babys von 0-12 Monaten</p>
    <div class="publisher-name">Lindhof Verlag</div>
    <div class="front-author">Helga Sturm</div>
  </section>
</div>
</body>
</html>
```